Bright Harbor Web Design & Marketing

Will award a 2nd place prize of $100.00 if someone can come up with a logo to match this design!
Updates

Okay, I'm really looking to see some better designs here. What do you think will bring the best designs out? Please remember with all future submissions I'm looking for a cartoon style / illustrator style website. I'm not sure what the technical term is for it, so I uploaded some images in the brief.

Target Market(s)

Small Business Owners

Industry/Entity Type

Marketing

Logo Text

BrightHarbor.com

Number of Pages Required

1 page

Colors

Designer to choose colors to be used in the design.

Requirements
Must have
• Logo should say BrightHarbor.com I would like more than just a text logo. I want some sort of cool custom graphic / icon with it that will look nice on shirts/hats/etc

```html
<!DOCTYPE html>
<html lang="en">
<head>
<meta charset="utf-8">
<title>Bright Harbor Web Design &amp; Marketing</title>
<link rel="stylesheet" href="https://fonts.googleapis.com/css2?family=Maven+Pro:wght@400;500;700&family=Tinos:wght@400;700&display=swap">
<style>
:root{
  --navy:#0e3a52;
  --navy-dark:#0a2c3f;
  --orange:#f7941d;
  --ink:#1d2a33;
  --text:#333;
  --muted:#777;
  --gray-bg:#f3f3f3;
  --line:#d8d8d8;
  --floor:#b87a40;
  --white:#fff;
  --head:'Maven Pro',sans-serif;
  --body:'Tinos',serif;
}
*{box-sizing:border-box;margin:0;padding:0}
html,body{width:1200px;height:4009px;overflow:hidden;background:var(--white)}
body{position:relative;font-family:var(--body);color:var(--text)}
section,header,footer,nav{position:absolute;left:0;width:1200px}
.abs{position:absolute}
.h2{font-family:var(--head);font-weight:700;font-size:31px;color:var(--ink)}
.h2 .accent{color:var(--orange)}
.center{left:0;width:1200px;text-align:center}
.lead{font-size:13px;line-height:20px;color:var(--text)}
.call-btn{position:absolute;display:flex;align-items:center;height:30px;padding:0 16px 0 4px;border-radius:15px;background:var(--navy);color:#fff;font-family:var(--head);font-weight:700;font-size:15px;gap:8px;white-space:nowrap}
.call-btn .dot{width:24px;height:24px;border-radius:50%;background:var(--orange);display:flex;align-items:center;justify-content:center}

/* header */
.site-header{top:0;height:85px}
.brand{left:150px;top:24px;display:flex;align-items:center;gap:10px;font-family:var(--head);font-weight:700;font-size:27px;color:var(--navy)}
.brand .mark{width:36px;height:36px;border-radius:50%;background:var(--orange)}
.phone{left:880px;top:28px;display:flex;align-items:center;gap:8px;font-family:var(--head);font-size:26px;color:var(--orange)}
.main-nav{top:85px;height:40px;background:var(--navy)}
.main-nav a{position:absolute;top:0;height:40px;line-height:40px;color:#fff;font-family:var(--head);font-size:14px;text-decoration:none;text-align:center}
.main-nav a.active{background:var(--orange)}

/* hero */
.hero{top:125px;height:465px;background:linear-gradient(180deg,#e9ecef 0%,#dfe3e7 55%,#cfd5da 100%)}
.hero-title{top:85px;font-family:var(--head);font-weight:700;font-size:30px;line-height:36px;color:var(--ink)}
.slide-arrow{position:absolute;top:228px;width:22px;height:22px;background:#333;color:#fff;font-size:12px;display:flex;align-items:center;justify-content:center}

/* about */
.about{top:590px;height:310px}
.about p{position:absolute;left:145px;width:520px;font-size:13px;line-height:20px}
.video{left:690px;top:55px;width:360px;height:205px;border-radius:6px;background:linear-gradient(180deg,#5b5f63,#3a3d40)}
.video .screen{position:absolute;left:22px;top:14px;right:22px;bottom:30px;background:#e9e9e9;display:flex;align-items:center;justify-content:center;font-family:var(--head);font-weight:700;font-size:22px;color:var(--navy)}

/* services */
.services{top:900px;height:555px;background:var(--gray-bg)}
.svc-menu{left:142px;top:190px;width:248px}
.svc-menu li{list-style:none;height:26px;margin-bottom:1px;background:var(--navy);color:#fff;font-family:var(--head);font-size:11px;display:flex;align-items:center;gap:8px;padding-left:8px}
.svc-menu li.on{background:var(--orange)}
.svc-menu li i{width:12px;height:12px;border:1px solid #fff;border-radius:2px}
.svc-detail{left:555px;top:210px;width:520px}
.svc-detail h4{font-family:var(--head);font-size:15px;font-weight:700;color:var(--navy);text-decoration:underline;margin-bottom:14px}
.svc-detail li{list-style:none;display:flex;gap:10px;font-size:11px;line-height:15px;margin-bottom:13px}
.tick{flex:none;width:14px;height:14px;background:var(--navy);color:#fff;font-size:10px;line-height:14px;text-align:center}

/* banner */
.banner{top:1455px;height:225px}

/* pricing */
.pricing{top:1680px;height:660px;background:var(--navy)}
.pricing-backdrop{position:absolute;left:0;top:0;width:1200px;height:520px;background:linear-gradient(180deg,#103e5a,#0c3349)}
.floor{position:absolute;left:0;top:520px;width:1200px;height:140px;background:linear-gradient(180deg,#c98a4b,#a8652e)}
.plan{position:absolute;width:204px;height:460px;background:#fff;border-top:3px solid var(--orange);box-shadow:0 4px 12px rgba(0,0,0,.35);text-align:center}
.plan .ring{width:54px;height:54px;border-radius:50%;border:2px solid;margin:28px auto 0}
.plan h3{font-family:var(--head);font-weight:500;font-size:17px;color:var(--ink);margin-top:20px}
.plan .from{font-size:12px;color:var(--muted);margin-top:32px}
.plan .price{font-family:var(--head);font-size:36px;margin-top:2px}
.plan .price sup,.plan .price small{font-size:13px}
.plan ul{text-align:left;margin:22px 0 0 24px}
.plan li{list-style:none;font-size:11px;line-height:24px}
.plan li:before{content:"› ";color:var(--orange)}
.plan .get{display:inline-block;margin-top:16px;width:124px;height:28px;line-height:28px;background:var(--orange);color:#fff;font-family:var(--head);font-size:13px}
.plan .get.dark{background:var(--navy)}
.plan .more{font-size:11px;margin-top:6px;font-family:var(--head)}
.plan .more b{display:inline-block;width:8px;height:8px;background:var(--orange);margin-left:22px}

/* clients */
.clients{top:2340px;height:255px}
.client-row{left:140px;top:160px;width:920px;display:flex;justify-content:space-between}
.client{display:flex;align-items:center;gap:6px;font-family:var(--head);font-weight:700;font-size:15px;color:#222}
.client i{width:14px;height:14px;border-radius:50%;background:#222}

/* why */
.why{top:2595px;height:495px;background:var(--gray-bg)}
.why-box{position:absolute;top:150px;width:145px;height:165px;background:#fff;box-shadow:0 2px 6px rgba(0,0,0,.12);text-align:center}
.why-box .icon{width:70px;height:70px;margin:20px auto 12px;border-radius:8px;background:#dfe8ee}
.why-box p{font-family:var(--head);font-size:11px;line-height:14px;color:var(--ink)}
.why-panel{left:150px;top:335px;width:900px;height:95px;background:#fff}
.why-panel h4{font-family:var(--head);font-size:14px;color:var(--navy);background:#eaeaea;padding:6px 12px}
.why-panel p{font-size:12px;line-height:18px;padding:4px 12px 0}

/* team */
.team{top:3090px;height:365px}
.member{position:absolute;top:165px;width:448px;height:145px;border:1px solid var(--line);background:#fff}
.member .photo{position:absolute;left:20px;top:14px;width:64px;height:64px;background:linear-gradient(180deg,#9aa3ab,#5e6870)}
.member h5{position:absolute;left:100px;top:30px;font-family:var(--head);font-size:13px;color:var(--ink)}
.member .role{position:absolute;left:100px;top:50px;font-family:var(--head);font-size:12px;color:var(--orange)}
.member p{position:absolute;left:20px;top:92px;width:410px;font-size:11px;line-height:16px}

/* inquiry */
.inquiry{top:3455px;height:405px}
.inq-photo{left:0;top:0;width:460px;height:405px;background:linear-gradient(135deg,#f2f2f2,#d5d9dc 60%,#b9bfc4)}
.field{position:absolute;font-size:11px;color:#444;border-bottom:1px solid var(--line);height:30px;width:250px}
.submit{left:495px;top:325px;width:86px;height:30px;background:var(--navy);color:#fff;font-family:var(--head);font-size:12px;text-align:center;line-height:30px}

/* footer */
.site-footer{top:3860px;height:149px;background:var(--navy)}
.f-item{position:absolute;top:30px;display:flex;gap:12px;color:#fff;font-size:11px;line-height:15px}
.f-item .ic{width:38px;height:38px;border-radius:50%;border:2px solid var(--orange);display:flex;align-items:center;justify-content:center}
.social{position:absolute;top:103px;left:880px;display:flex;gap:8px}
.social span{width:20px;height:20px;border-radius:50%;border:1px solid #8aa}
</style>
</head>
<body>

<header class="site-header">
  <div class="abs brand"><span class="mark"></span>BrightHarbor.com</div>
  <div class="abs phone">
    <svg width="24" height="24" viewBox="0 0 24 24"><path fill="#f7941d" d="M6.6 10.8a15 15 0 0 0 6.6 6.6l2.2-2.2c.3-.3.7-.4 1-.2 1.1.4 2.3.6 3.6.6.6 0 1 .4 1 1V20c0 .6-.4 1-1 1A17 17 0 0 1 3 4c0-.6.4-1 1-1h3.5c.6 0 1 .4 1 1 0 1.3.2 2.5.6 3.6.1.3 0 .7-.2 1z"/></svg>
    123-456-7890
  </div>
</header>

<nav class="main-nav">
  <a class="active" style="left:145px;width:115px">HOME</a>
  <a style="left:310px;width:170px">SERVICES &amp; PRICING</a>
  <a style="left:560px;width:120px">OUR TEAM</a>
  <a style="left:820px;width:120px">CLIENTS</a>
  <a style="left:990px;width:130px">CONTACT US</a>
</nav>

<section class="hero" role="img" aria-label="Illustration of a designer desk with laptops, books, coffee cups and charts">
  <div class="abs hero-title center">The Design &amp; Marketing Team That Always Puts Trust &amp; Loyalty<br>Before Profits</div>
  <div class="call-btn" style="left:515px;top:178px"><span class="dot"><svg width="12" height="12" viewBox="0 0 24 24"><path fill="#fff" d="M6.6 10.8a15 15 0 0 0 6.6 6.6l2.2-2.2c.3-.3.7-.4 1-.2 1.1.4 2.3.6 3.6.6.6 0 1 .4 1 1V20c0 .6-.4 1-1 1A17 17 0 0 1 3 4c0-.6.4-1 1-1h3.5c.6 0 1 .4 1 1 0 1.3.2 2.5.6 3.6.1.3 0 .7-.2 1z"/></svg></span>Call Us Today</div>
  <div class="slide-arrow" style="left:6px">‹</div>
  <div class="slide-arrow" style="right:6px">›</div>
</section>

<section class="about">
  <h2 class="abs h2" style="left:145px;top:42px;font-size:29px">ABOUT BRIGHT HARBOR <span class="accent">Web Design</span></h2>
  <p style="top:102px">We believe that honesty and integrity come before personal profits. We are a family owned and operated company. Our parents raised us to take care of each other and that's exactly what we've done. We treat each of our clients with the same loyalty and respect that we give each other.</p>
  <p style="top:200px">We are not looking to have hundreds and hundreds of clients. We are looking to expand our family with a handful of like-minded individuals. Companies who take pride in their work and their customers. We want to build mutually beneficial, lucrative, and long term partnerships.</p>
  <div class="abs video" role="img" aria-label="Laptop showing an intro video">
    <div class="screen">
      <svg width="40" height="40" viewBox="0 0 40 40" style="margin-right:10px"><circle cx="20" cy="20" r="19" fill="#222"/><path d="M16 12l12 8-12 8z" fill="#fff"/></svg>
      BrightHarbor.com
    </div>
  </div>
</section>

<section class="services">
  <h2 class="abs h2 center" style="top:52px">SERVICES <span class="accent">We Provide</span></h2>
  <p class="abs lead" style="left:155px;width:890px;top:105px;text-align:center">Lorem ipsum dolor sit amet, consectetuer adipiscing elit, sed diam nonummy nibh euismod tincidunt ut laoreet dolore magna aliquam erat volutpat. Ut wisi enim ad minim veniam, quis nostrud exerci.</p>
  <svg class="abs" style="left:80px;top:190px" width="20" height="50" viewBox="0 0 20 50"><circle cx="8" cy="8" r="5" fill="none" stroke="#4a90c2" stroke-width="2"/><path d="M12 12l5 5" stroke="#4a90c2" stroke-width="2"/><circle cx="8" cy="36" r="5" fill="none" stroke="#4a90c2" stroke-width="2"/><path d="M12 40l5 5" stroke="#4a90c2" stroke-width="2"/></svg>
  <ul class="abs svc-menu">
    <li class="on"><i></i>Website Design &amp; Management</li>
    <li><i></i>Logo Design &amp; Branding Materials</li>
    <li><i></i>Online Store Design &amp; Management</li>
    <li><i></i>Local Seo Management</li>
    <li><i></i>Search Engine Optimization</li>
    <li><i></i>Social Media Marketing</li>
    <li><i></i>Marketing Material &amp; Print Design</li>
    <li><i></i>Outsourcing Management</li>
    <li><i></i>Consulting Service</li>
  </ul>
  <svg class="abs" style="left:418px;top:185px" width="100" height="90" viewBox="0 0 100 90"><rect x="4" y="8" width="80" height="55" rx="3" fill="none" stroke="#555" stroke-width="5"/><rect x="34" y="63" width="20" height="12" fill="#555"/><rect x="24" y="75" width="40" height="5" fill="#555"/><path d="M60 40L92 4" stroke="#555" stroke-width="6"/></svg>
  <div class="abs svc-detail">
    <h4>Website Design &amp; Management</h4>
    <ul>
      <li><span class="tick">✓</span>Lorem ipsum dolor sit amet, consectetuer adipiscing elit, sed diam nonummy nibh euismod</li>
      <li><span class="tick">✓</span>Lorem dolor sit amet, consectetuer adipiscing</li>
      <li><span class="tick">✓</span>Lorem ipsum dolor sit amet, consectetuer adipiscing elit, sed diam nonummy nibh euismod</li>
      <li><span class="tick">✓</span>Lorem ipsum dolor sit amet, consectetuer adipiscing elit, sed diam nonummy nibh<br>euismod.nonummy dolor sit amet.</li>
    </ul>
  </div>
  <div class="abs" style="left:575px;top:378px;font-family:var(--head);font-weight:700;font-size:15px;color:var(--orange)">We have answers</div>
  <div class="call-btn" style="left:555px;top:410px;height:26px;font-size:13px;border-radius:13px;width:305px"><span class="dot" style="width:20px;height:20px"></span>Call Us Today To Avail The Service</div>
</section>

<section class="banner">
  <h2 class="abs h2 center" style="top:35px;font-weight:500;font-size:33px">Lorem ipsum dolor sit amet consectetuer</h2>
  <p class="abs center" style="top:85px;font-size:18px;line-height:26px;padding:0 170px">Lorem ipsum dolor sit amet consectetuer &nbsp;adipiscing elit sed diam the nonummy nibh sit amet consectetuer adipiscing elit sed consectetuer.</p>
  <div class="call-btn" style="left:515px;top:155px"><span class="dot"></span>Call Us Today</div>
</section>

<section class="pricing">
  <div class="pricing-backdrop" role="img" aria-label="Dark blue wall backdrop"></div>
  <div class="floor" role="img" aria-label="Wooden floor"></div>
  <h2 class="abs h2 center" style="top:45px;color:#fff;font-weight:500">OUR &nbsp;Pricing</h2>
  <div class="plan" style="left:160px;top:145px">
    <div class="ring" style="border-color:#f7941d"></div><h3>Basic Plan</h3>
    <div class="from">Starting from</div><div class="price" style="color:#f7941d"><sup>$</sup>52<small>.99</small></div>
    <ul><li>Lorem Ipsum Dolar Ipsum</li><li>Lorem Ipsum Dolar</li><li>Lorem Ipsum Dolar Ipsum</li><li>Lorem Ipsum Dolar</li></ul>
    <span class="get dark">Get Started &nbsp;→</span><div class="more">More Information <b></b></div>
  </div>
  <div class="plan" style="left:395px;top:130px">
    <div class="ring" style="border-color:#e8493a"></div><h3>Standard Plan</h3>
    <div class="from">Starting from</div><div class="price" style="color:#e8493a"><sup>$</sup>114<small>.00</small></div>
    <ul><li>Lorem Ipsum Dolar Ipsum</li><li>Lorem Ipsum Dolar</li><li>Lorem Ipsum Dolar Ipsum</li><li>Lorem Ipsum Dolar</li></ul>
    <span class="get">Get Started &nbsp;→</span><div class="more">More Information <b></b></div>
  </div>
  <div class="plan" style="left:623px;top:145px">
    <div class="ring" style="border-color:#8dc63f"></div><h3>Gold Plan</h3>
    <div class="from">Starting from</div><div class="price" style="color:#8dc63f"><sup>$</sup>200<small>.99</small></div>
    <ul><li>Lorem Ipsum Dolar Ipsum</li><li>Lorem Ipsum Dolar</li><li>Lorem Ipsum Dolar Ipsum</li><li>Lorem Ipsum Dolar</li></ul>
    <span class="get">Get Started &nbsp;→</span><div class="more">More Information <b></b></div>
  </div>
  <div class="plan" style="left:855px;top:145px">
    <div class="ring" style="border-color:#3aa3e3"></div><h3>Platinum Plan</h3>
    <div class="from">Starting from</div><div class="price" style="color:#3aa3e3"><sup>$</sup>490<small>.00</small></div>
    <ul><li>Lorem Ipsum Dolar Ipsum</li><li>Lorem Ipsum Dolar</li><li>Lorem Ipsum Dolar Ipsum</li><li>Lorem Ipsum Dolar</li></ul>
    <span class="get">Get Started &nbsp;→</span><div class="more">More Information <b></b></div>
  </div>
</section>

<section class="clients">
  <h2 class="abs h2 center" style="top:35px">OUR <span class="accent">Valuable Clients</span></h2>
  <p class="abs lead center" style="top:88px;padding:0 155px">Lorem ipsum dolor sit amet, consectetuer adipiscing elit, sed diam nonummy nibh euismod tincidunt ut laoreet dolore magna aliquam erat volutpat. Ut wisi enim ad minim.</p>
  <div class="abs" style="left:110px;top:160px;font-size:22px;color:#aaa">‹</div>
  <div class="abs client-row">
    <span class="client"><i></i>Maplecrest</span>
    <span class="client"><i></i>Northvale</span>
    <span class="client"><i></i>Northvale</span>
    <span class="client" style="border:1px solid #ddd;padding:4px 8px">Lumora</span>
    <span class="client"><i></i>Maplecrest</span>
    <span class="client"><i></i>Pinecliff</span>
    <span class="client">Tallbridge</span>
    <span class="client">Tallbridge</span>
  </div>
  <div class="abs" style="left:1070px;top:160px;font-size:22px;color:#aaa">›</div>
</section>

<section class="why">
  <h2 class="abs h2 center" style="top:35px">WHY <span class="accent">CHoose Us</span></h2>
  <p class="abs lead center" style="top:85px;padding:0 155px">Lorem ipsum dolor sit amet, consectetuer adipiscing elit, sed diam nonummy nibh euismod tincidunt ut laoreet dolore magna aliquam erat volutpat. Ut wisi enim ad minim veniam, quis nostrud exerci.</p>
  <div class="why-box" style="left:155px"><div class="icon" role="img" aria-label="Money back icon"></div><p>100% Risk Free<br>Investment</p></div>
  <div class="why-box" style="left:353px"><div class="icon" role="img" aria-label="Loyalty card icon"></div><p>Customer Loyalty<br>Program</p></div>
  <div class="why-box" style="left:527px"><div class="icon" role="img" aria-label="Support clock icon"></div><p>24/7 U.S Based<br>Customer Support</p></div>
  <div class="why-box" style="left:700px"><div class="icon" role="img" aria-label="Personal service icon"></div><p>Unmatched Personal<br>Service</p></div>
  <div class="why-box" style="left:882px"><div class="icon" role="img" aria-label="Payment options icon"></div><p>Multiple Payment<br>Options Available</p></div>
  <svg class="abs" style="left:765px;top:322px" width="16" height="12"><path d="M0 12L8 0l8 12z" fill="#f7941d"/></svg>
  <div class="abs why-panel">
    <h4>Unmatched Personal Service</h4>
    <p>Do you need us to come to your office to help train staff on the management of your new website, content management system, or computer software?<br>That's not a problem.<br>We welcome to you and provide hands on training.</p>
  </div>
</section>

<section class="team">
  <h2 class="abs h2 center" style="top:45px">OUR <span class="accent">Team</span></h2>
  <p class="abs lead center" style="top:95px;padding:0 155px">Lorem ipsum dolor sit amet, consectetuer adipiscing elit, sed diam nonummy nibh euismod tincidunt ut laoreet dolore magna aliquam erat volutpat. Ut wisi enim ad minim veniam, quis nostrud exerci.</p>
  <div class="abs" style="left:110px;top:230px;font-size:22px;color:#aaa">‹</div>
  <div class="member" style="left:142px">
    <div class="photo" role="img" aria-label="Portrait photo of team member"></div>
    <h5>DANIEL HARLOW</h5><div class="role">Chief Executive Officer</div>
    <p>Lorem ipsum dolor sit amet, consectetuer adipiscing elit, sed diam nonummy nibh euismod tincidunt ut laoreet dolore magna aliquam....[+]</p>
  </div>
  <div class="member" style="left:625px">
    <div class="photo" role="img" aria-label="Portrait photo of team member"></div>
    <h5>OWEN PRESCOTT</h5><div class="role">Chief Operations Officer</div>
    <p>Lorem ipsum dolor sit amet, consectetuer adipiscing elit, sed diam nonummy nibh euismod tincidunt ut laoreet dolore magna aliquam....[+]</p>
  </div>
  <div class="abs" style="left:1070px;top:230px;font-size:22px;color:#aaa">›</div>
</section>

<section class="inquiry">
  <div class="abs inq-photo" role="img" aria-label="Photo of hands typing on a laptop with a coffee cup and plant"></div>
  <h2 class="abs h2" style="left:495px;top:58px">QUICK <span class="accent">Inquiry</span></h2>
  <div class="field" style="left:495px;top:112px">First Name</div>
  <div class="field" style="left:768px;top:112px">Last Name</div>
  <div class="field" style="left:495px;top:162px">Email</div>
  <div class="field" style="left:768px;top:162px">Phone Number</div>
  <div class="abs" style="left:495px;top:212px;font-size:11px;color:#444">Details About Your Enquiry</div>
  <div class="abs" style="left:495px;top:235px;width:520px;height:75px;border:1px solid var(--line)"></div>
  <div class="abs submit">SUBMIT</div>
</section>

<footer class="site-footer">
  <div class="f-item" style="left:215px">
    <span class="ic"><svg width="16" height="18" viewBox="0 0 16 20"><path d="M8 0a7 7 0 0 0-7 7c0 5 7 13 7 13s7-8 7-13a7 7 0 0 0-7-7zm0 10a3 3 0 1 1 0-6 3 3 0 0 1 0 6z" fill="#fff"/></svg></span>
    <div><b>Bright Harbor Web Design</b><br>Street Name, City Name<br>State Zip code</div>
  </div>
  <div class="f-item" style="left:530px">
    <span class="ic"><svg width="16" height="16" viewBox="0 0 24 24"><path fill="#fff" d="M6.6 10.8a15 15 0 0 0 6.6 6.6l2.2-2.2c.3-.3.7-.4 1-.2 1.1.4 2.3.6 3.6.6.6 0 1 .4 1 1V20c0 .6-.4 1-1 1A17 17 0 0 1 3 4c0-.6.4-1 1-1h3.5c.6 0 1 .4 1 1 0 1.3.2 2.5.6 3.6.1.3 0 .7-.2 1z"/></svg></span>
    <div><b>Phone:</b><br>+012 3456 789</div>
  </div>
  <div class="f-item" style="left:790px">
    <span class="ic"><svg width="18" height="14" viewBox="0 0 18 14"><rect x="1" y="1" width="16" height="12" fill="none" stroke="#fff" stroke-width="1.5"/><path d="M1 1l8 7 8-7" fill="none" stroke="#fff" stroke-width="1.5"/></svg></span>
    <div><b>Email:</b><br>inquiry@brightharbor.com</div>
  </div>
  <div class="abs" style="left:222px;top:110px;color:#fff;font-size:10px">Copyright © 2017 BRIGHT HARBOR WEB DESIGN. All Rights Reserved.</div>
  <div class="social"><span></span><span></span><span></span><span></span><span></span></div>
</footer>

</body>
</html>
```